Kestrel Hearth Business Card Design

Design new, 2 sides, business cards for a residential and light commercial heating, air conditioning contractor.

Target Market(s)

Homeowners, small businesses

Industry/Entity Type

Business

Contact Information for Business Card

Dominic Westerhall
Phone - 862-415-2736
Email
Address - PO box 518
Brightwater NJ 07912
Website - www.KestrelHearthLLC.example

Requirements
Must have
• logo, company colors, standard size with no die cut, so I can use nova stamp

```html
<!DOCTYPE html>
<html lang="en">
<head>
<meta charset="utf-8">
<title>Kestrel Hearth Business Card</title>
<link rel="stylesheet" href="https://fonts.googleapis.com/css2?family=Tinos:wght@400;700&family=Arimo:wght@400&display=swap">
<style>
  :root {
    --crimson: #a2233b;
    --orange: #f58a1f;
    --white: #ffffff;
    --backdrop: #e8e4dd;
    --shadow: rgba(0, 0, 0, 0.18);
  }
  * { box-sizing: border-box; margin: 0; padding: 0; }
  html, body { width: 1200px; height: 950px; overflow: hidden; }
  body {
    background: var(--backdrop);
    display: flex;
    flex-direction: column;
    align-items: center;
    justify-content: center;
    gap: 50px;
  }
  .card {
    position: relative;
    width: 735px;
    height: 420px;
    overflow: hidden;
    box-shadow: 0 6px 18px var(--shadow);
  }
  .card-front {
    background: var(--white);
    display: flex;
    align-items: center;
    justify-content: center;
  }
  .brand-name {
    font-family: "Tinos", "Times New Roman", serif;
    font-weight: 700;
    color: var(--crimson);
    text-transform: uppercase;
    letter-spacing: 1px;
    text-align: center;
    line-height: 1.05;
  }
  .card-front .brand-name { font-size: 54px; }
  .card-back { background: var(--crimson); }
  .shield-panel { position: absolute; inset: 0; }
  .contact-block {
    position: absolute;
    left: 48px;
    top: 44px;
    color: var(--white);
    font-family: "Arimo", Arial, sans-serif;
    font-size: 17px;
    line-height: 1.45;
  }
  .person-name {
    font-family: "Tinos", "Times New Roman", serif;
    color: var(--orange);
    font-size: 24px;
    text-transform: uppercase;
    letter-spacing: 1px;
    line-height: 1.1;
  }
  .person-title {
    font-family: "Tinos", "Times New Roman", serif;
    font-size: 17px;
    text-transform: uppercase;
    letter-spacing: 1px;
    margin-bottom: 14px;
  }
  .address { margin-bottom: 6px; }
  .contact-line { display: flex; align-items: center; gap: 10px; }
  .contact-line svg { width: 15px; height: 15px; flex: none; fill: var(--orange); }
  .card-back .brand-name {
    position: absolute;
    left: 450px;
    top: 220px;
    width: 260px;
    font-size: 38px;
  }
</style>
</head>
<body>

  <section class="card card-front" aria-label="Business card front">
    <p class="brand-name">Kestrel<br>Hearth</p>
  </section>

  <section class="card card-back" aria-label="Business card back">
    <svg class="shield-panel" viewBox="0 0 735 420" aria-hidden="true">
      <path d="M385 150 L470 178 L530 112 L745 112 L745 430 L500 430 C445 385 420 320 435 250 C440 215 420 180 385 150 Z"
            fill="var(--white)" stroke="var(--orange)" stroke-width="14" stroke-linejoin="round"/>
    </svg>

    <div class="contact-block">
      <p class="person-name">Dominic Westerhall</p>
      <p class="person-title">President</p>
      <p class="address">PO box 518<br>Brightwater NJ 07912</p>
      <p class="contact-line">
        <svg viewBox="0 0 16 16"><path d="M3 1h3l1.5 4-2 1.2a9 9 0 0 0 4.3 4.3L11 8.5l4 1.5v3a2 2 0 0 1-2 2A12 12 0 0 1 1 3a2 2 0 0 1 2-2z"/></svg>
        862-415-2736
      </p>
      <p class="contact-line">
        <svg viewBox="0 0 16 16"><path d="M4 0h8a1 1 0 0 1 1 1v14a1 1 0 0 1-1 1H4a1 1 0 0 1-1-1V1a1 1 0 0 1 1-1zm1 2v10h6V2zm3 11a1 1 0 1 0 0 2 1 1 0 0 0 0-2z"/></svg>
        862-415-2740
      </p>
      <p class="contact-line">
        <svg viewBox="0 0 16 16"><path d="M4 0h7v4H4zM1 5h14v7h-3v4H4v-4H1zm4 5v4h6v-4z"/></svg>
        862-415-2751
      </p>
      <p class="contact-line">
        <svg viewBox="0 0 16 16"><path d="M0 3h16v10H0zm1.5 1.2V5L8 9l6.5-4v-.8L8 8z"/></svg>
        dominic@kestrelhearth.example
      </p>
      <p class="contact-line">
        <svg viewBox="0 0 16 16"><path d="M8 0a8 8 0 1 0 0 16A8 8 0 0 0 8 0zm0 1.5c.9 0 2 1.8 2.3 5H5.7C6 3.3 7.1 1.5 8 1.5zM5.7 8h4.6c-.3 3.2-1.4 5-2.3 5S6 11.2 5.7 8zM1.6 8h2.6c.1 1.9.5 3.5 1.1 4.6A6.5 6.5 0 0 1 1.6 8zm0-1.5a6.5 6.5 0 0 1 3.7-4.6c-.6 1.1-1 2.7-1.1 4.6zm10.2 0c-.1-1.9-.5-3.5-1.1-4.6a6.5 6.5 0 0 1 3.7 4.6zm0 1.5h2.6a6.5 6.5 0 0 1-3.7 4.6c.6-1.1 1-2.7 1.1-4.6z"/></svg>
        www.KestrelHearthLLC.example
      </p>
    </div>

    <p class="brand-name">Kestrel<br>Hearth</p>
  </section>

</body>
</html>
```